Business Card Design using new attached logo

We are a family run Plumbing and Heating firm looking to improve our company image with an improved business card and new logo.We are looking to keep the company colour (Blue) involved in our design

Reason: New logo added which needs to be incorporated on designs

Industry/Entity Type

Business

Contact Information for Business Card

See attachment of all info required.

Requirements
Must have
• We have just picked a new company logo which is attached.
• Could you please provide your business card designs using this logo.
• We are looking for the logo on the back as well as the front with all the info required

```html
<!DOCTYPE html>
<html lang="en">
<head>
<meta charset="utf-8">
<title>Calder Services – Business Card</title>
<link rel="stylesheet" href="https://fonts.googleapis.com/css2?family=Marcellus+SC&family=Source+Sans+3:ital,wght@0,400;0,600;1,400&display=swap">
<style>
  :root {
    --backdrop: #333333;
    --blue-deep: #1f3c7c;
    --blue-mid: #2d63aa;
    --blue-light: #3b86cc;
    --swoosh-grey: #8a8a8a;
    --paper: #ffffff;
    --ink: #222222;
    --icon: #2a4f8f;
    --divider: #cfcfcf;
  }
  * { box-sizing: border-box; margin: 0; padding: 0; }
  html, body {
    width: 1200px; height: 907px; overflow: hidden;
    background: var(--backdrop);
    font-family: "Source Sans 3", Arial, sans-serif;
  }
  .card {
    position: absolute; left: 300px; width: 600px; height: 343px;
    box-shadow: 0 4px 10px rgba(0,0,0,0.55);
    overflow: hidden;
  }
  .card-front { top: 92px; background: var(--paper); }
  .card-back {
    top: 472px;
    background: radial-gradient(ellipse 60% 75% at 50% 40%, var(--blue-light) 0%, var(--blue-mid) 45%, var(--blue-deep) 100%);
  }
  .front-band { position: absolute; inset: 0; width: 600px; height: 343px; }
  .holder {
    position: absolute; left: 29px; top: 22px; color: var(--paper);
    font-family: "Marcellus SC", Georgia, serif; line-height: 1.1;
  }
  .holder-name { font-size: 24px; letter-spacing: 0.5px; }
  .holder-role { font-size: 18px; letter-spacing: 0.5px; }
  .brand {
    position: absolute; color: var(--blue-deep); font-weight: 600;
    font-family: "Source Sans 3", Arial, sans-serif; text-align: center;
  }
  .brand-name { display: block; line-height: 0.9; }
  .brand-sub { display: block; }
  .card-front .brand { left: 34px; top: 190px; width: 240px; }
  .card-front .brand-name { font-size: 62px; }
  .card-front .brand-sub { font-size: 17px; letter-spacing: 9px; margin-top: 4px; }
  .divider {
    position: absolute; left: 295px; top: 151px; width: 1px; height: 164px;
    background: var(--divider);
  }
  .contact {
    position: absolute; left: 318px; top: 143px; color: var(--ink);
    font-size: 15px; line-height: 19.5px;
  }
  .contact-address { margin-bottom: 8px; }
  .contact-list { list-style: none; }
  .contact-list li { display: flex; align-items: center; height: 22.5px; }
  .contact-list svg { width: 15px; height: 15px; margin-right: 8px; fill: var(--icon); flex: none; }
  .card-back .brand {
    color: var(--paper); left: 150px; width: 300px; top: 124px;
  }
  .card-back .brand-name { font-size: 72px; }
  .card-back .brand-sub { font-size: 19px; letter-spacing: 10px; margin-top: 4px; }
  .tagline {
    position: absolute; left: 0; width: 100%; top: 282px; text-align: center;
    color: var(--paper); font-style: italic; font-size: 16px; letter-spacing: 0.3px;
  }
</style>
</head>
<body>
  <section class="card card-front">
    <svg class="front-band" viewBox="0 0 600 343" aria-hidden="true">
      <defs>
        <linearGradient id="bandGradient" x1="0" y1="0" x2="1" y2="0">
          <stop offset="0" stop-color="#234787"/>
          <stop offset="0.5" stop-color="#3b84c9"/>
          <stop offset="1" stop-color="#1f3c7c"/>
        </linearGradient>
      </defs>
      <path d="M0,203 C170,75 420,38 600,60 V52 C420,22 180,58 0,175 Z" fill="var(--swoosh-grey)"/>
      <path d="M0,0 H600 V52 C420,22 180,58 0,175 Z" fill="url(#bandGradient)"/>
    </svg>
    <div class="holder">
      <div class="holder-name">Martin Hale</div>
      <div class="holder-role">Director</div>
    </div>
    <div class="brand">
      <span class="brand-name">Calder</span>
      <span class="brand-sub">SERVICES</span>
    </div>
    <div class="divider"></div>
    <div class="contact">
      <address class="contact-address" style="font-style:normal">
        Calder Services Ltd<br>
        14 Mill Row, Hartley Lane<br>
        Northfield, NF27QP
      </address>
      <ul class="contact-list">
        <li><svg viewBox="0 0 16 16"><path d="M4 1 L6.5 4.5 L5 6.5 C6 9 7.5 10.5 9.5 11.5 L11.5 10 L15 12.5 L13.5 15 C7 14.5 1.5 9 1 2.5 Z"/></svg>020 7946 0321</li>
        <li><svg viewBox="0 0 16 16"><rect x="4" y="1" width="8" height="5"/><rect x="1" y="6" width="14" height="6" rx="1"/><rect x="4" y="10" width="8" height="5" fill="#fff" stroke="#2a4f8f"/></svg>020 7946 0458</li>
        <li><svg viewBox="0 0 16 16"><rect x="4" y="0.5" width="8" height="15" rx="1.5"/><rect x="5.5" y="3" width="5" height="6" fill="#fff"/></svg>07700900614</li>
        <li><svg viewBox="0 0 16 16"><rect x="1" y="3.5" width="14" height="9"/><path d="M1 3.5 L8 9 L15 3.5" fill="none" stroke="#fff" stroke-width="1.3"/></svg>martinhale@calderservices.co.uk</li>
        <li><svg viewBox="0 0 16 16"><circle cx="8" cy="8" r="6.5" fill="none" stroke="#2a4f8f" stroke-width="1.2"/><ellipse cx="8" cy="8" rx="3" ry="6.5" fill="none" stroke="#2a4f8f" stroke-width="1"/><path d="M1.5 8 H14.5 M2.5 5 H13.5 M2.5 11 H13.5" stroke="#2a4f8f" stroke-width="1"/></svg>www.calderservices.co.uk</li>
      </ul>
    </div>
  </section>

  <section class="card card-back">
    <div class="brand">
      <span class="brand-name">Calder</span>
      <span class="brand-sub">SERVICES</span>
    </div>
    <p class="tagline">Plumbing and Heating Services</p>
  </section>
</body>
</html>
```